Fun, Clean Business Card For Family Focused Travel Agency

I need a business card using specific colors and fonts as in the uploaded files. Ideally, I would like a large image of the logo on the back and all the contact info on the front. Maybe the stars/dots somewhere in a flowy form.

I do want it the contact information to be clear and easy to read. I don't want it to look too busy. Maybe even a bit minimalist.

I plan or ordering the ROUNDED CORNER business cards from Cardwell Press, so please consider that in your design.

Target Market(s)

Families with children, couples, groups of friends

Contact Information for Business Card

Marla Quint, Owner
Marla@TumbleTrips.example
Cell Phone Number 555-218-4603
Office Phone Number 555-647-1925
Specializing in Glimmerland destinations, Pelican Bay Fun Park, Cruises and All-Inclusive Vacations.

Nice but not required:
www.TumbleTrips.example
Facebook, Instagram, Twitter icons with username: TumbleTrips

Font styles to use
Sans Serif

Requirements
Must have
• Please try to use the colors from the logo as much as possible. I understand lighter shades/colors may be needed for some things.
Should not have
• NO SERIF FONTS. That is really the only thing I do not want at all

```html
<!DOCTYPE html>
<html lang="en">
<head>
<meta charset="utf-8">
<title>Tumble Trips – Business Card</title>
<link href="https://fonts.googleapis.com/css2?family=Open+Sans:wght@400;600;700&family=Kaushan+Script&display=swap" rel="stylesheet">
<style>
  :root {
    --navy: #0b1534;
    --navy-deep: #070d24;
    --navy-light: #16224a;
    --teal: #1fb495;
    --orange: #f08a2c;
    --sky: #3aa6dd;
    --white: #ffffff;
    --backdrop: #2a2a2c;
  }
  * { margin: 0; padding: 0; box-sizing: border-box; }
  html, body { width: 1200px; height: 892px; overflow: hidden; }
  body {
    background: var(--backdrop);
    font-family: "Open Sans", Arial, sans-serif;
    position: relative;
  }
  .card {
    position: absolute;
    left: 250px;
    width: 700px;
    height: 400px;
    border-radius: 22px;
    overflow: hidden;
  }
  /* Back of card */
  .card-back {
    top: 30px;
    background: linear-gradient(160deg, var(--navy-light) 0%, var(--navy) 45%, var(--navy-deep) 100%);
    color: var(--white);
    text-align: center;
  }
  .social-row {
    position: absolute;
    top: 24px;
    right: 30px;
    display: flex;
    gap: 5px;
  }
  .social-dot {
    width: 15px; height: 15px;
    border-radius: 50%;
    background: var(--white);
  }
  .back-brand {
    position: absolute;
    top: 118px;
    left: 0; right: 0;
    display: flex;
    justify-content: center;
    align-items: center;
    gap: 12px;
    font-weight: 700;
    font-size: 44px;
    letter-spacing: 0.5px;
  }
  .brand-dot {
    width: 22px; height: 22px;
    border-radius: 50%;
    background: var(--teal);
  }
  .specialty-label {
    position: absolute;
    top: 210px;
    left: 0; right: 0;
    font-family: "Kaushan Script", cursive;
    font-size: 30px;
  }
  .specialty-list {
    position: absolute;
    top: 262px;
    left: 0; right: 0;
    font-size: 17px;
    line-height: 1.45;
  }
  /* Front of card */
  .card-front {
    top: 462px;
    background: var(--navy);
    color: var(--white);
  }
  .front-art {
    position: absolute;
    inset: 0;
  }
  .front-brand {
    position: absolute;
    top: 90px;
    left: 390px;
    display: flex;
    align-items: center;
    gap: 12px;
    font-weight: 700;
    font-size: 40px;
    color: var(--navy);
  }
  .contact-block {
    position: absolute;
    left: 40px;
    top: 248px;
  }
  .contact-name {
    font-weight: 700;
    font-size: 26px;
    letter-spacing: 0.5px;
    line-height: 1.05;
  }
  .contact-title {
    font-weight: 600;
    font-size: 15px;
    letter-spacing: 0.5px;
    margin-bottom: 8px;
  }
  .contact-list { list-style: none; }
  .contact-list li {
    display: flex;
    align-items: center;
    gap: 10px;
    font-size: 16px;
    line-height: 1.4;
  }
  .contact-icon { width: 15px; height: 15px; flex: none; }
</style>
</head>
<body>

<section class="card card-back" aria-label="Card back">
  <div class="social-row">
    <span class="social-dot"></span><span class="social-dot"></span><span class="social-dot"></span>
  </div>
  <div class="back-brand"><span class="brand-dot"></span>Tumble Trips</div>
  <p class="specialty-label">Specializing in</p>
  <p class="specialty-list">Glimmerland destinations • Pelican Bay Fun Park<br>Cruises &amp; All-Inclusive Vacations.</p>
</section>

<section class="card card-front" aria-label="Card front">
  <svg class="front-art" viewBox="0 0 700 400" width="700" height="400" aria-hidden="true">
    <path d="M165 0 C 260 120, 420 230, 700 262 L700 0 Z" fill="var(--white)"/>
    <path d="M165 0 C 260 120, 420 230, 700 262 L700 272 C 410 248, 240 130, 135 0 Z" fill="var(--teal)"/>
    <path d="M190 38 C 300 150, 450 252, 700 275" fill="none" stroke="var(--sky)" stroke-width="3"/>
    <path d="M180 34 C 290 160, 440 262, 700 282" fill="none" stroke="var(--orange)" stroke-width="2.5"/>
    <path d="M185 40 C 300 165, 450 268, 700 288" fill="none" stroke="var(--white)" stroke-width="1.5" opacity="0.7"/>
  </svg>
  <div class="front-brand"><span class="brand-dot"></span>Tumble Trips</div>
  <div class="contact-block">
    <p class="contact-name">MARLA QUINT</p>
    <p class="contact-title">OWNER</p>
    <ul class="contact-list">
      <li>
        <svg class="contact-icon" viewBox="0 0 16 16"><path d="M2 5c0-2 2-3 6-3s6 1 6 3l-3 1-1-2H6L5 6zM4 8h8l1 6H3z" fill="var(--white)"/></svg>
        555-647-1925
      </li>
      <li>
        <svg class="contact-icon" viewBox="0 0 16 16"><rect x="4" y="1" width="8" height="14" rx="1.5" fill="none" stroke="var(--white)" stroke-width="1.6"/><circle cx="8" cy="12.5" r="0.9" fill="var(--white)"/></svg>
        555-218-4603
      </li>
      <li>
        <svg class="contact-icon" viewBox="0 0 16 16"><rect x="1" y="3" width="14" height="10" fill="var(--white)"/><path d="M1 3l7 6 7-6" fill="none" stroke="var(--navy)" stroke-width="1.4"/></svg>
        Marla@TumbleTrips.example
      </li>
      <li>
        <svg class="contact-icon" viewBox="0 0 16 16"><circle cx="8" cy="8" r="7" fill="var(--white)"/><path d="M1 8h14M8 1c-3 3-3 11 0 14M8 1c3 3 3 11 0 14" fill="none" stroke="var(--navy)" stroke-width="1.1"/></svg>
        www.TumbleTrips.example
      </li>
    </ul>
  </div>
</section>

</body>
</html>
```